Local Flower Farm Needs Business Card Design

I need business cards designed for a flower farm based in Eudora, Kansas.
Business Info:
We are a local cut flower farm located in Eudora, Kansas, founded by Corinne Haldwick. What started as a passion for agriculture and search for more joy in daily life has blossomed into a small business dedicated to providing the community with beautiful, fresh, and sustainable flowers. We specialize in local, seasonal blooms, ensuring that every petal reflects the care and dedication we pour into our craft. Our mission is to deliver the highest quality flowers directly to our customers through local farmers markets and to florists who share our commitment to sustainability. Join us in celebrating the beauty of nature, one bloom at a time!
Contact Details:
Corinne Haldwick
Owner
Phone 913-555-0147
Facebook: Rosalind Thorpe Gardens
Instagram: @RosalindThorpeGardens
Website: RosalindThorpeGardens.example
Target Market(s)
Wholesale to Florists and Direct to Consumer via Farmers Market
Industry/Entity Type
Florist, Farm
Contact Information for Business Card
Name, Contact Info, Logo
Look and feel
Each slider illustrates characteristics of the customer's brand and the style your logo design should communicate.

```html
<!DOCTYPE html>
<html lang="en">
<head>
<meta charset="UTF-8">
<title>Rosalind Thorpe Gardens – Business Card</title>
<link href="https://fonts.googleapis.com/css2?family=Montserrat:wght@400;500;700&display=swap" rel="stylesheet">
<style>
  :root {
    --backdrop: #ece8e1;
    --card-white: #ffffff;
    --ink-teal: #0f2b2e;
    --ink-body: #1a1a1a;
    --deep-teal: #0a2a2f;
    --teal-emboss: #1d4a50;
    --faint-grey: #e2e2e2;
  }
  * { margin: 0; padding: 0; box-sizing: border-box; }
  html, body { width: 900px; height: 1200px; overflow: hidden; }
  body {
    background: var(--backdrop);
    font-family: "Montserrat", sans-serif;
    position: relative;
  }
  .card {
    position: absolute;
    left: 80px;
    width: 742px;
    height: 442px;
    border-radius: 22px;
    overflow: hidden;
    box-shadow: 0 10px 24px rgba(0,0,0,0.18);
  }
  .card--front { top: 130px; background: var(--card-white); }
  .card--back { top: 638px; background: var(--deep-teal); }

  .brand-seal {
    position: absolute;
    left: 34px; top: 46px;
    width: 226px; height: 226px;
    border: 1.5px solid var(--ink-teal);
    border-radius: 50%;
    display: flex; align-items: center; justify-content: center;
    text-align: center;
  }
  .brand-seal__name {
    font-weight: 700;
    font-size: 22px;
    line-height: 1.25;
    color: var(--ink-teal);
    letter-spacing: 1px;
  }

  .holder {
    position: absolute;
    right: 50px; top: 46px;
    text-align: right;
  }
  .holder__name { font-weight: 700; font-size: 26px; color: var(--ink-teal); }
  .holder__role { font-weight: 400; font-size: 16px; color: var(--ink-body); margin-top: 4px; }

  .contact-list {
    position: absolute;
    left: 38px; top: 308px;
    list-style: none;
  }
  .contact-list li {
    display: flex; align-items: center; gap: 9px;
    font-size: 16px; color: var(--ink-body);
    height: 26px;
  }
  .contact-list svg { width: 15px; height: 15px; flex: none; }

  .brand-watermark {
    position: absolute;
    left: 470px; top: 190px;
    width: 230px;
    font-weight: 700;
    font-size: 38px;
    line-height: 1.1;
    color: var(--faint-grey);
    text-align: center;
  }

  .back-seal {
    position: absolute;
    left: 202px; top: 62px;
    width: 340px; height: 340px;
    border: 2px solid var(--teal-emboss);
    border-radius: 50%;
    display: flex; align-items: center; justify-content: center;
    text-align: center;
  }
  .back-seal__name {
    font-weight: 700;
    font-size: 34px;
    line-height: 1.2;
    letter-spacing: 1px;
    color: var(--teal-emboss);
  }
</style>
</head>
<body>
  <section class="card card--front">
    <div class="brand-seal">
      <span class="brand-seal__name">Rosalind<br>Thorpe<br>Gardens</span>
    </div>

    <div class="holder">
      <p class="holder__name">Corinne Haldwick</p>
      <p class="holder__role">Owner</p>
    </div>

    <ul class="contact-list">
      <li>
        <svg viewBox="0 0 24 24" aria-hidden="true"><path fill="var(--ink-body)" d="M6.6 10.8a15.1 15.1 0 0 0 6.6 6.6l2.2-2.2a1 1 0 0 1 1-.25 11.4 11.4 0 0 0 3.6.57 1 1 0 0 1 1 1V20a1 1 0 0 1-1 1A17 17 0 0 1 3 4a1 1 0 0 1 1-1h3.5a1 1 0 0 1 1 1c0 1.25.2 2.45.57 3.6a1 1 0 0 1-.25 1z"/></svg>
        913-555-0147
      </li>
      <li>
        <svg viewBox="0 0 24 24" aria-hidden="true"><circle cx="12" cy="12" r="10" fill="var(--ink-body)"/></svg>
        Rosalind Thorpe Gardens
      </li>
      <li>
        <svg viewBox="0 0 24 24" aria-hidden="true"><circle cx="12" cy="12" r="10" fill="var(--ink-body)"/></svg>
        @RosalindThorpeGardens
      </li>
      <li>
        <svg viewBox="0 0 24 24" aria-hidden="true"><g fill="none" stroke="var(--ink-body)" stroke-width="2"><circle cx="12" cy="12" r="9.5"/><ellipse cx="12" cy="12" rx="4" ry="9.5"/><path d="M2.5 12h19"/></g></svg>
        www.RosalindThorpeGardens.example
      </li>
    </ul>

    <div class="brand-watermark">Rosalind Thorpe Gardens</div>
  </section>

  <section class="card card--back">
    <div class="back-seal">
      <span class="back-seal__name">Rosalind<br>Thorpe<br>Gardens</span>
    </div>
  </section>
</body>
</html>
```